Commercial Loan Originator Business Card (CHANGE COLORS SCHEME)

CHANGE COLOR SCHEME - SAME DESIGN

Name Marlene Agate
Title Commercial Loan Originator
Office (800) 417-2906 x68
Direct (240) 615-2043
Email freshgreens4life@quillbox.example

Name Dale Morrow
Office (800) 417-2906 x70
Direct (410) 392-5184
Email d.morthehomeguy@quillbox.example

Name Leonard Vasko
Office (800) 417-2906 x71
Direct (215) 463-0712
Email l.vasko41@quillbox.example

Name Gwen Halsey
Office (800) 417-2906 x
Direct (202) 548-1370
Email ghalsey63@quillbox.example

Name Mirna Ashby
Office (800) 417-2906 x72
Direct (240) 871-4526
Email tristatehomelending@quillbox.example

```html
<!DOCTYPE html>
<html lang="en">
<head>
<meta charset="utf-8">
<title>Dale Morrow – Business Card</title>
<link href="https://fonts.googleapis.com/css2?family=Montserrat:wght@400;700&display=swap" rel="stylesheet">
<style>
  :root {
    --stage: #e6e8e6;
    --card: #ffffff;
    --accent: #0e6b55;
    --accent-deep: #0a4a3b;
    --ink: #26302d;
    --muted: #4d5753;
    --photo-a: #6f7d72;
    --photo-b: #2a312d;
  }
  * { margin: 0; padding: 0; box-sizing: border-box; }
  html, body {
    width: 1200px; height: 788px; overflow: hidden;
    background: var(--stage);
    font-family: "Montserrat", sans-serif;
  }
  .business-card {
    position: absolute;
    left: 150px; top: 137px;
    width: 900px; height: 514px;
    background: var(--card);
    border: 4px solid var(--accent);
    border-radius: 28px;
    overflow: hidden;
    box-shadow: 0 10px 30px rgba(0,0,0,0.12);
  }
  .identity { position: absolute; left: 52px; top: 134px; width: 470px; }
  .person-name {
    color: var(--accent-deep);
    font-weight: 700;
    font-size: 34px;
    letter-spacing: 0.4px;
    text-transform: uppercase;
    line-height: 1;
    white-space: nowrap;
  }
  .person-title {
    color: var(--muted);
    font-weight: 400;
    font-size: 18px;
    margin-top: 8px;
    letter-spacing: 0.3px;
    white-space: nowrap;
  }
  .divider {
    width: 16px; height: 2px;
    background: var(--accent);
    margin: 20px 0;
  }
  .contact-list { list-style: none; }
  .contact-item {
    display: flex; align-items: center; gap: 12px;
    color: var(--ink);
    font-size: 19px;
    font-weight: 400;
    margin-bottom: 14px;
    letter-spacing: 0.2px;
    white-space: nowrap;
  }
  .contact-icon { width: 20px; height: 20px; flex: none; fill: var(--accent); }
  .portrait {
    position: absolute;
    right: 0; bottom: 0;
    width: 340px; height: 440px;
    border-radius: 24px 0 0 0;
    background: linear-gradient(170deg, var(--photo-a) 0%, var(--photo-b) 100%);
  }
</style>
</head>
<body>
  <section class="business-card">
    <div class="identity">
      <h1 class="person-name">Dale Morrow</h1>
      <p class="person-title">Commercial Loan Originator</p>
      <div class="divider"></div>
      <ul class="contact-list">
        <li class="contact-item">
          <svg class="contact-icon" viewBox="0 0 24 24" aria-hidden="true"><path d="M6.6 10.8a15.1 15.1 0 0 0 6.6 6.6l2.2-2.2a1 1 0 0 1 1-.25 11.4 11.4 0 0 0 3.6.57 1 1 0 0 1 1 1V20a1 1 0 0 1-1 1A17 17 0 0 1 3 4a1 1 0 0 1 1-1h3.5a1 1 0 0 1 1 1c0 1.25.2 2.45.57 3.57a1 1 0 0 1-.25 1z"/></svg>
          (800) 417-2906 x70
        </li>
        <li class="contact-item">
          <svg class="contact-icon" viewBox="0 0 24 24" aria-hidden="true"><path d="M7 2h10a2 2 0 0 1 2 2v16a2 2 0 0 1-2 2H7a2 2 0 0 1-2-2V4a2 2 0 0 1 2-2zm0 3v13h10V5zm5 14.2a1 1 0 1 0 0 .01z"/></svg>
          (410) 392-5184
        </li>
        <li class="contact-item">
          <svg class="contact-icon" viewBox="0 0 24 24" aria-hidden="true"><path d="M3 5h18a1 1 0 0 1 1 1v12a1 1 0 0 1-1 1H3a1 1 0 0 1-1-1V6a1 1 0 0 1 1-1zm1 2.4V17h16V7.4l-8 5.6z"/></svg>
          d.morthehomeguy@quillbox.example
        </li>
      </ul>
    </div>
    <div class="portrait" role="img" aria-label="Portrait photo of Dale Morrow in a green blazer and dark shirt"></div>
  </section>
</body>
</html>
```